A5 Magazine Cover Design

I need a front cover designing for a new community magazine called ORLEEN. ORLEEN will be listing local buisnesses and local interest articles for the residents in my area. I need the look to be clean but inviting.

I will consider any colour combination as long as its not too bright.

```html
<!DOCTYPE html>
<html lang="en">
<head>
<meta charset="UTF-8">
<title>ORLEEN — Community Magazine Cover</title>
<link rel="stylesheet" href="https://fonts.googleapis.com/css2?family=Open+Sans:wght@700;800&display=swap">
<style>
  :root {
    --navy: #011628;
    --navy-soft: #0a2239;
    --navy-haze: #06203a;
    --teal: #2d5866;
    --teal-deep: #234c5a;
    --ice: #e3fdff;
  }
  html, body {
    margin: 0;
    padding: 0;
    width: 846px;
    height: 1200px;
    overflow: hidden;
    background: var(--navy);
  }
  .cover {
    display: block;
    width: 846px;
    height: 1200px;
  }
  .cover__ground { fill: var(--navy); }
  .cover__haze { fill: var(--navy-haze); opacity: 0.55; }
  .cover__floor { fill: var(--navy-soft); }
  .cover__band { fill: var(--teal); }
  .cover__rail { fill: var(--teal); }
  .cover__bubble { fill: var(--teal-deep); }
  .masthead {
    font-family: "Open Sans", sans-serif;
    font-weight: 800;
    fill: var(--ice);
    letter-spacing: -6px;
  }
  .tagline {
    font-family: "Open Sans", sans-serif;
    font-weight: 700;
    fill: var(--teal);
  }
</style>
</head>
<body>
<svg class="cover" viewBox="0 0 1000 1419" preserveAspectRatio="none" xmlns="http://www.w3.org/2000/svg">
  <rect class="cover__ground" x="0" y="0" width="1000" height="1419"/>
  <polygon class="cover__haze" points="0,750 1000,0 1000,120 0,900"/>
  <polygon class="cover__floor" points="0,1340 1000,1205 1000,1419 0,1419"/>

  <g class="cover__rails">
    <rect class="cover__rail" x="932" y="0" width="18" height="260"/>
    <rect class="cover__rail" x="932" y="480" width="18" height="735" rx="9"/>
    <rect class="cover__rail" x="963" y="480" width="24" height="939"/>
  </g>

  <polygon class="cover__band" points="0,385 1000,238 1000,495 0,645"/>

  <text class="masthead" x="75" y="595" font-size="285" textLength="880" lengthAdjust="spacingAndGlyphs" transform="rotate(-8.6 75 595)">ORLEEN</text>
  <text class="tagline" x="155" y="657" font-size="36" textLength="785" lengthAdjust="spacingAndGlyphs" transform="rotate(-8.6 155 657)">searches , reviews and recommends locally</text>

  <g class="cover__bubbles">
    <circle class="cover__bubble" cx="190" cy="1165" r="133"/>
    <circle class="cover__bubble" cx="0" cy="1265" r="150"/>
    <circle class="cover__bubble" cx="100" cy="1419" r="70"/>
    <circle class="cover__bubble" cx="418" cy="1144" r="35"/>
    <circle class="cover__bubble" cx="537" cy="1057" r="17"/>
    <circle class="cover__bubble" cx="574" cy="1272" r="33"/>
    <circle class="cover__bubble" cx="433" cy="1345" r="75"/>
  </g>
</svg>
</body>
</html>
```